Graphic Design Project

ok I have the artwork for my presentation folder, and I have the text to put on the folder, I need you to apply text to the folder and the single sheets, so inside the artwork is pictures to use, text to use. thank you so much ask me as many questions as you need
Updates

my girl forgot to upload the mock ups of the presentation folder and single sheets, my apologies please check updated files

Hey Guys this is a eazy project the artwork is done, the text is done, the pictures are done!, all you have to do is assemble the project, I even have mock up pictures of how project looks finished, I have made the money good so that you would not pass on this project because it is not that creative of a job!

Target Market(s)

Dr's and patients

Industry/Entity Type

Graphic Design

Requirements
Must have
• use the single sheet artwork to make as many single sheets as you need to use all of the text supplied
Should not have
• do not make this, so professional looking that it does not appeal to the patients

```html
<!DOCTYPE html>
<html lang="en">
<head>
<meta charset="utf-8">
<title>Why Use KindPath Counseling – Single Sheet</title>
<link rel="stylesheet" href="https://fonts.googleapis.com/css2?family=Tinos:ital,wght@0,400;0,700;1,400;1,700&family=Open+Sans:wght@700&display=swap">
<style>
  :root {
    --backdrop: #7a5a3c;
    --paper: #ffffff;
    --panel-grey: #d4d4d6;
    --panel-sand: #dcd3c1;
    --ink: #1c1c1c;
    --brand-brown: #8b5a2b;
    --brand-grey: #6a6a6a;
    --seal-fill: #c4c4c6;
    --seal-ring: #8d8d8f;
  }
  * { margin: 0; padding: 0; box-sizing: border-box; }
  html, body {
    width: 1200px; height: 840px; overflow: hidden;
    background: var(--backdrop);
  }
  .canvas { position: relative; width: 1200px; height: 840px; }

  .sheet {
    position: absolute; top: 118px;
    background: var(--paper);
    font-family: "Tinos", "Times New Roman", serif;
    color: var(--ink);
    overflow: hidden;
  }
  .sheet--front { left: 46px; width: 512px; height: 670px; }
  .sheet--back  { left: 595px; width: 519px; height: 672px; }
  .sheet__panels { position: absolute; inset: 0; }
  .sheet__content { position: absolute; inset: 0; }

  .title {
    position: absolute; left: 0; right: 0; top: 36px;
    text-align: center; font-size: 30px; line-height: 38px; font-weight: 700;
  }
  .brand-lead { color: var(--brand-brown); }
  .brand-tail { color: var(--brand-grey); }
  .muted-qq { font-weight: 400; }

  .copy { position: absolute; font-size: 11.5px; line-height: 16px; }
  .copy .agency { color: var(--brand-brown); }
  .headlines {
    position: absolute; left: 0; right: 0; top: 141px;
    text-align: center; font-style: italic; font-size: 11.5px; line-height: 16px;
  }

  .mark {
    position: absolute; left: 0; right: 0; top: 228px;
    display: flex; justify-content: center; align-items: center; gap: 10px;
  }
  .mark__dot {
    width: 48px; height: 48px; border-radius: 50%;
    background: var(--seal-fill); border: 2px solid var(--seal-ring);
  }
  .mark__name { font-size: 15px; font-weight: 700; color: var(--ink); }

  .front-cta {
    position: absolute; left: 0; right: 0; top: 598px;
    text-align: center; font-family: "Open Sans", Arial, sans-serif;
    font-weight: 700; font-size: 14px; line-height: 20px;
  }

  .board-label { position: absolute; left: 0; right: 0; top: 108px; text-align: center; font-size: 17px; line-height: 22px; }
  .seal {
    position: absolute; left: 204px; top: 156px; width: 112px; height: 112px;
    border-radius: 50%; background: var(--seal-fill); border: 3px solid var(--seal-ring);
  }
  .guideline-title { position: absolute; left: 0; right: 0; top: 291px; text-align: center; font-style: italic; font-size: 11.5px; line-height: 15px; }
  .guideline-lead { position: absolute; left: 0; right: 0; top: 310px; text-align: center; font-weight: 700; font-size: 13.5px; line-height: 18px; }
  .steps { position: absolute; left: 36px; right: 17px; top: 341px; font-size: 11.5px; line-height: 15.5px; }
  .steps p { margin-bottom: 3px; }
  .steps em { font-weight: 700; }
  .back-cta { position: absolute; left: 0; right: 0; top: 485px; text-align: center; font-size: 18px; line-height: 22px; color: var(--brand-brown); }
  .back-sub { position: absolute; left: 0; right: 0; top: 520px; text-align: center; font-size: 13px; line-height: 17px; font-weight: 700; }
  .back-body { position: absolute; left: 40px; right: 107px; text-align: center; font-size: 11.5px; line-height: 15px; }
</style>
</head>
<body>
<main class="canvas">

  <section class="sheet sheet--front">
    <svg class="sheet__panels" width="512" height="670" viewBox="0 0 512 670" aria-hidden="true">
      <path d="M0 0 H474 L512 36 V300 L470 470 Q458 540 420 555 H0 Z" fill="var(--panel-grey)"/>
      <path d="M0 561 H420 L444 572 L420 670 H0 Z" fill="var(--panel-sand)"/>
      <path d="M512 395 V585 H472 Q462 585 465 572 L508 398 Q510 395 512 395 Z" fill="var(--panel-sand)"/>
      <rect x="462" y="615" width="70" height="80" rx="14" fill="var(--panel-grey)"/>
    </svg>
    <div class="sheet__content">
      <h1 class="title">Why Use <span class="brand-lead">Kind</span><span class="brand-tail">Path</span> Counseling??</h1>
      <p class="copy" style="left:26px; right:36px; top:94px;">Unbalanced and misleading media coverage on the abuse of opioid analgesics only perpetuates misconceptions about Pain Management;</p>
      <div class="headlines">
        <p>"Feds raid pill mills; arrest docs"</p>
        <p>"Agents Raid Clinics in Drug Crackdown"</p>
        <p>"11 arrested as part of multi-agency pill mill raid"</p>
      </div>
      <div class="mark">
        <span class="mark__dot"></span><span class="mark__name">NDCA</span>
      </div>
      <p class="copy" style="left:26px; right:42px; top:332px;"><span class="agency">Office of Misuse Prevention</span> exists to educate and increase public awareness of the potential for the abuse of prescription and over-the-counter medicines and encourage increased diligence by Doctors and Mental health care providers to keep these products from being abused or misused.</p>
      <p class="copy" style="left:26px; right:42px; top:402px;"><span class="agency">NDCA</span> has strongly supported the establishment of "Model Guidelines for the Use of Controlled Substances in Pain Management" by the Alliance of Regional Medical Councils. These guidelines reflect accepted standards that may be used by both medical professionals and regulators in determining the appropriateness of opioid prescribing.</p>
      <p class="copy" style="left:26px; right:78px; top:474px;">The <span class="agency">NDCA</span> states there are no specific guidelines concerning what is required to support a conclusion that an accused doctor acted outside the usual course of professional practice when prescribing medicines for pain. Rather, the courts must engage in a case-by-case analysis of evidence to determine whether a reasonable inference of guilt may be drawn from specific facts.</p>
      <p class="front-cta">Can you afford Not to Use <span class="brand-lead">Kind</span><span class="brand-tail">Path</span> Counseling??</p>
    </div>
  </section>

  <section class="sheet sheet--back">
    <svg class="sheet__panels" width="519" height="672" viewBox="0 0 519 672" aria-hidden="true">
      <path d="M0 0 H490 L519 22 V325 L473 473 Q468 476 458 476 H0 Z" fill="var(--panel-grey)"/>
      <path d="M0 482 H455 Q464 482 466 488 L411 672 H0 Z" fill="var(--panel-sand)"/>
      <path d="M519 400 V585 H465 Q460 585 461 578 L515 403 Q517 400 519 400 Z" fill="var(--panel-sand)"/>
      <rect x="460" y="612" width="80" height="80" rx="16" fill="var(--panel-grey)"/>
    </svg>
    <div class="sheet__content">
      <h1 class="title">Why Use <span class="brand-lead">Kind</span><span class="brand-tail">Path</span> Counseling<span class="muted-qq">??</span></h1>
      <p class="board-label">"The Medical Board"</p>
      <div class="seal"></div>
      <p class="guideline-title">Guidelines for the Use of Controlled Substances for the Treatment of Pain:</p>
      <p class="guideline-lead">"The board has 10 steps to treat pain and 4 steps relate to KindPath Counseling"</p>
      <div class="steps">
        <p><em>Step Two Reads:</em>&nbsp; Consider referrals to appropriate specialists, such as addictionologist, psy&shy;chiatrists, etc...&nbsp; The result of the referral should be included in the patient's chart.</p>
        <p><em>Step Five Reads:</em>&nbsp; Take the time to explain the relative risks and benefits of the drug and record in the chart the fact that this was done.</p>
        <p><em>Step Nine Reads:</em> Maintaining adequate records is extremely important. The physician who carefully manages pain treatment and maintains detailed records which reflect all the steps involved in the process</p>
        <p><em>Step Ten Reads:</em>&nbsp; DOCUMENT..DOCUMENT... DOCUMENT</p>
      </div>
      <p class="back-cta">Can you afford Not to Use KindPath Counseling??</p>
      <p class="back-sub">Why Use <span class="brand-lead">Kind</span><span class="brand-tail">Path</span> Counseling??</p>
      <p class="back-body" style="top:543px;">Lets say your worst case scenario happens, your Patient dies and the family<br>blames and Sues you!</p>
      <p class="back-body" style="top:586px;">Can you afford not to have KindPath Pro Active Addiction Counseling in your<br>Chart, Documenting<br>Opiod Education and Addiction Prevention Assessments??<br>Document.. Document.. Document</p>
    </div>
  </section>

</main>
</body>
</html>
```